Förderverein einer Kirchengemeinde sucht Flyer-Design
Zielgruppe
Wir sind ein Förderverein einer Kirchengemeinde, der sich für die kirchenmusikalische Arbeit einsetzt.
Wir wünschen uns ein niveauvolles und zeitgemäßes/modernes Flyerdesign, das die etablierten Konzertbesucher anspricht, aber vor allem auch Menschen erreicht und überzeugt, die (noch) nichts mit Kirche zu tun haben.
Das Alter der (Haupt-) Zielgruppe (Männer und Frauen) erstreckt sich von 45 bis 70 Jahren.
Aufgabenstellung
Bei der Wahl des Formates würden wir (aus der Sicht von Laien) ein zweimal gefaltetes DIN A4 quer Format nehmen. Aber wir lassen uns gerne überraschen und sind grundsätzlich für andere Lösungen offen.
Bitte den Abschnitt für Adress- und sonstige Dateneintragungen samt Kontodaten so gestalten und platzieren, dass man ihn leicht abtrennen und verschicken kann.
Der Flyer soll Kirchenmusik als lebendig und attraktiv darstellen und neue (jüngere) Mitglieder für den Freundeskreis werben.
Lassen Sie die Bilder sprechen!!

```html
<!DOCTYPE html>
<html lang="de">
<head>
<meta charset="utf-8">
<title>Förderkreis Tonkunst – Beitrittserklärung</title>
<link href="https://fonts.googleapis.com/css2?family=Mulish:ital,wght@0,400;0,600;0,700;0,800;1,400&display=swap" rel="stylesheet">
<style>
:root{
  --bg:#e4e4e4;
  --paper:#ffffff;
  --red:#c1272d;
  --title-red:#d3202a;
  --ink:#4a4a4a;
  --ink-soft:#5c5c5c;
  --rule:#cfcfcf;
  --band:#e2e2e2;
  --white:#ffffff;
}
*{margin:0;padding:0;box-sizing:border-box}
html,body{width:1200px;height:837px;overflow:hidden;background:var(--bg);font-family:"Mulish",sans-serif;color:var(--ink)}
.flyer{position:absolute;left:15px;top:8px;width:1170px;height:821px;display:flex}
.form-panel{position:relative;width:705px;height:100%;background:var(--paper);border-right:1.5px dashed #777}
.info-panel{position:relative;width:465px;height:100%;background:var(--red);color:var(--white)}

.form-title{position:absolute;left:33px;top:20px;font-size:26px;font-weight:700;color:var(--title-red);letter-spacing:.2px}
.field-table{position:absolute;left:32px;width:643px;border:1px solid var(--rule);font-size:13.5px;color:var(--ink-soft)}
.contact{top:64px}
.row{display:flex;border-bottom:1px solid var(--rule)}
.row:last-child{border-bottom:none}
.cell{flex:1;padding:9px 7px 0;height:33px}
.cell + .cell{border-left:1px solid var(--rule)}
.cell.tall{height:65px;position:relative}
.cell.tall::after{content:"";position:absolute;left:7px;right:10px;bottom:10px;border-bottom:1px solid var(--rule)}
.cell.sign{height:58px}

.band{position:absolute;left:32px;width:643px;height:31px;background:var(--band);font-weight:700;font-size:16.5px;color:var(--ink);padding:6px 8px}
.band.fees{top:314px}
.band.sepa{top:472px;height:30px;border:1px solid var(--rule);border-bottom:none}

.options{position:absolute;top:352px;font-size:15.5px;color:var(--ink-soft);line-height:24px;letter-spacing:.2px}
.options.left{left:38px}
.options.right{left:340px;line-height:30px}
.opt{display:flex;align-items:center;gap:5px;white-space:nowrap}
.box{width:14px;height:14px;border:1.3px solid #8a8a8a;flex:none}
.opt .blank{display:inline-block;width:142px;border-bottom:1px solid var(--rule);height:18px;margin-left:4px}
.note{font-style:italic;font-size:13px;padding-left:18px}

.sepa-table{top:502px;border-top:none}
.sepa-table .cell{height:41px;padding-top:13px}
.mandate{padding:10px 7px 0;height:95px;font-size:14px;line-height:18px;position:relative;width:100%}
.mandate .sign-line{position:absolute;left:7px;right:14px;top:66px;display:flex;align-items:flex-end;gap:28px}
.mandate .sign-line span{flex:1;border-bottom:1px solid var(--rule);height:12px}
.collect{height:34px;padding:9px 7px 0;font-style:italic;font-size:12.5px}

.bank{position:absolute;left:31px;top:744px;display:flex;gap:12px;font-size:12.5px;color:var(--ink-soft);line-height:22px}
.bank dt{font-size:16px;font-weight:600;color:var(--ink);line-height:20px}

.cut-hint{position:absolute;right:2px;top:693px;display:flex;flex-direction:column;align-items:center;gap:4px}
.cut-hint span{writing-mode:vertical-rl;transform:rotate(180deg);font-size:7px;color:#777}

.organ-photo{position:absolute;left:0;top:0;width:100%;height:409px;background:linear-gradient(180deg,#d8d3c6 0%,#c8b9a0 30%,#b56f6a 60%,#d9d4cc 100%)}
.brand{position:absolute;left:52px;top:436px;display:flex;align-items:center;gap:10px;font-size:18px;font-weight:700;letter-spacing:.3px}
.brand .mark{width:12px;height:12px;background:var(--white)}
.intro{position:absolute;left:52px;top:488px;width:400px;font-size:18px;line-height:22px;font-weight:400}
.intro strong{font-weight:700}
.address{position:absolute;left:101px;top:598px;font-size:19.5px;line-height:24px;font-weight:700;font-style:normal}
.address .gap{margin-top:12px}
.more{position:absolute;left:52px;top:750px;font-size:17.5px;line-height:25px}
.more strong{font-weight:700;font-size:19px}
</style>
</head>
<body>
<main class="flyer">
  <section class="form-panel">
    <h1 class="form-title">Beitrittserklärung</h1>

    <div class="field-table contact">
      <div class="row"><div class="cell">Name, Vorname</div></div>
      <div class="row"><div class="cell">Institution/Firma</div></div>
      <div class="row"><div class="cell tall">Straße, Hausnr., PLZ, Ort</div></div>
      <div class="row"><div class="cell">Telefon/Mobil</div><div class="cell">Geburtsdatum</div></div>
      <div class="row"><div class="cell tall sign">E-Mail</div><div class="cell tall sign">Datum, Unterschrift</div></div>
    </div>

    <h2 class="band fees">Mitgliedsbeiträge</h2>
    <div class="options left">
      <div class="opt"><span class="box"></span>Einzelpersonen € 20,-</div>
      <div class="opt"><span class="box"></span>Ehepaare/Partnerschaften € 32,-</div>
      <div class="opt"><span class="box"></span>Institutionen/Firmen € 95,-</div>
      <div class="note">(jeweils Mindestbeiträge)</div>
    </div>
    <div class="options right">
      <div class="opt"><span class="box"></span>&nbsp;Gewünschter Betrag: €<span class="blank"></span></div>
      <div class="opt"><span class="box"></span>&nbsp;Einmalige Spende <i>(ohne Mitgliedschaft)</i></div>
      <div class="opt"><span class="box"></span>&nbsp;Ich benötige eine Spendenbescheinigung</div>
    </div>

    <h2 class="band sepa">SEPA-Lastschriftmandat</h2>
    <div class="field-table sepa-table">
      <div class="row"><div class="cell" style="flex:1.55">IBAN</div><div class="cell">BIC</div></div>
      <div class="row"><div class="cell">Kreditinstitut</div><div class="cell">Kontoinhaber</div></div>
      <div class="row"><div class="mandate">Hiermit ermächtige ich den Förderkreis Tonkunst den von mir zu entrichtenden<br>Mitgliedsbeitrag von meinem Konto einzuziehen
        <div class="sign-line">Ort, Datum, Unterschrift<span></span></div></div></div>
      <div class="row"><div class="collect">Der Einzug der Mitgliedsbeiträge erfolgt zu Beginn eines Kalenderjahres</div></div>
    </div>

    <dl class="bank">
      <dt>Spendenkonto:</dt>
      <dd>Sparkasse Lindenfeld<br>IBAN: DE00 1234 5678 9012 3456 78<br>BIC: SPKLDE21XXX</dd>
    </dl>

    <div class="cut-hint">
      <svg width="12" height="14" viewBox="0 0 12 14" fill="none" stroke="#666" stroke-width="1.1">
        <circle cx="3" cy="11" r="2"/><circle cx="9" cy="11" r="2"/>
        <line x1="4" y1="9.5" x2="9" y2="1"/><line x1="8" y1="9.5" x2="3" y2="1"/>
      </svg>
      <span>Hier abtrennen</span>
    </div>
  </section>

  <section class="info-panel">
    <div class="organ-photo" role="img" aria-label="Foto der barocken Orgel mit vergoldeten Verzierungen und silbernen Pfeifen"></div>
    <div class="brand"><span class="mark"></span><span>Förderkreis Tonkunst</span></div>
    <p class="intro">Wenn Sie die Kirchenmusik an St. Lamberti<br>als Mitglied im <strong>Förderkreis Tonkunst</strong><br>fördern möchten, senden Sie die ausgefüllte<br>Beitrittserklärung an den</p>
    <address class="address">
      Förderkreis Tonkunst<br>
      Kirchengemeinde St. Lamberti<br>
      Lindenallee 7, 12345 Lindenfeld
      <div class="gap">Tel.: 01234-5678-90<br>m.wendler@kirche-lindenfeld.de</div>
    </address>
    <p class="more">Nähere Informationen finden Sie unter<br><strong>www.tonkunst-lindenfeld.de</strong></p>
  </section>
</main>
</body>
</html>
```